Business Card Design for a Personal Trainer

I need a business card design for my job as a personal trainer. It should have a unique, modern and exclusive design. On the front there should be only my logo with my name and my job. 0162/3819204 Tobias Lendhart Wiesengrundweg 14 80417 Munich Germany The most important contact information is the web adress. it can be bigger than the rest, but its not necessary. The card should be 8,5cmx5,5cm big. Font: Roboto. Colors: black, white, gray, 56c1ff.

```html
<!DOCTYPE html>
<html lang="de">
<head>
<meta charset="utf-8">
<title>Tobias Lendhart – Personal Trainer Visitenkarten</title>
<link href="https://fonts.googleapis.com/css2?family=Roboto:wght@300;400;500&family=Libre+Baskerville:wght@700&display=swap" rel="stylesheet">
<style>
  :root {
    --page-bg: #e4e4e4;
    --card-black: #1c1c1c;
    --card-gray-light: #5e5e5e;
    --card-gray-dark: #333333;
    --white: #ffffff;
    --text-light: #f0f0f0;
    --accent: #a8184c;
    --frame: #c4c4c4;
  }
  * { box-sizing: border-box; margin: 0; padding: 0; }
  html, body {
    width: 1200px; height: 864px; overflow: hidden;
    background: var(--page-bg);
    font-family: "Roboto", Arial, sans-serif;
  }
  .canvas { position: relative; width: 1200px; height: 864px; }

  .card {
    position: absolute; width: 580px; height: 375px;
    overflow: hidden;
    box-shadow: 0 10px 24px rgba(0,0,0,0.25);
  }
  .card--back  { left: 580px; top: 50px;  background: var(--card-black); }
  .card--front { left: 40px;  top: 450px;
    background: radial-gradient(ellipse at 30% 40%, var(--card-gray-light), var(--card-gray-dark) 85%); }

  /* brand lockup */
  .brand { position: absolute; text-align: center; color: var(--white); }
  .brand__mark {
    width: 18px; height: 18px; background: var(--white);
    margin: 0 auto 10px;
  }
  .brand__name {
    font-weight: 400; font-size: 30px; letter-spacing: 0.5px;
    line-height: 1; white-space: nowrap;
  }
  .brand__tagline {
    display: flex; align-items: center; gap: 6px;
    font-weight: 400; font-size: 11px; letter-spacing: 3px;
    margin-top: 4px;
  }
  .brand__tagline::before, .brand__tagline::after {
    content: ""; flex: 1; height: 1px; background: var(--white);
  }

  .card--back .brand { left: 150px; width: 280px; top: 40px; }
  .web {
    position: absolute; color: var(--accent);
    font-weight: 400; font-size: 20px; letter-spacing: 1px; white-space: nowrap;
  }
  .card--back .web { left: 0; width: 580px; text-align: center; top: 162px; }

  .gallery {
    position: absolute; left: 30px; right: 30px; top: 215px;
    display: flex; justify-content: space-between;
  }
  .gallery__frame {
    width: 162px; height: 116px; background: var(--frame); padding: 8px;
  }
  .gallery__photo { width: 100%; height: 100%; }
  .gallery__photo--lifting { background: linear-gradient(135deg, #8a8a8a, #4a4a4a); }
  .gallery__photo--football { background: linear-gradient(160deg, #d8d8d8, #3f6b3a 60%, #2e5a2c); }
  .gallery__photo--rowing { background: linear-gradient(135deg, #2a2a2a, #6b5a4a); }

  /* front */
  .card--front .brand { left: 35px; width: 280px; top: 26px; }
  .contact {
    position: absolute; left: 20px; width: 300px; top: 150px;
    text-align: right; color: var(--text-light);
  }
  .contact__name {
    font-family: "Libre Baskerville", Georgia, serif; font-weight: 700;
    font-size: 19px; letter-spacing: 1.5px; text-align: center;
    padding-left: 40px; margin-bottom: 6px;
  }
  .contact .web { position: static; font-size: 20px; margin-bottom: 12px; text-align: center; padding-left: 20px; }
  .contact__line { font-size: 16px; font-weight: 400; line-height: 1.45; letter-spacing: 0.3px; white-space: nowrap; }

  .portrait {
    position: absolute; right: 0; bottom: 0; width: 250px; height: 330px;
    background: radial-gradient(ellipse at 50% 70%, #4a4a4a, #2e2e2e 70%, transparent 100%);
  }
</style>
</head>
<body>
<main class="canvas">

  <section class="card card--back">
    <div class="brand">
      <div class="brand__mark"></div>
      <div class="brand__name">TOBIAS LENDHART</div>
      <div class="brand__tagline">PERSONAL TRAINER</div>
    </div>
    <div class="web">www.tobiaslendhart.de</div>
    <div class="gallery">
      <div class="gallery__frame"><div class="gallery__photo gallery__photo--lifting" role="img" aria-label="Photo of an athlete lifting a barbell in a gym"></div></div>
      <div class="gallery__frame"><div class="gallery__photo gallery__photo--football" role="img" aria-label="Photo of a football boot on grass in front of a goal net"></div></div>
      <div class="gallery__frame"><div class="gallery__photo gallery__photo--rowing" role="img" aria-label="Photo of a person training on a rowing machine"></div></div>
    </div>
  </section>

  <section class="card card--front">
    <div class="brand">
      <div class="brand__mark"></div>
      <div class="brand__name">TOBIAS LENDHART</div>
      <div class="brand__tagline">PERSONAL TRAINER</div>
    </div>
    <div class="contact">
      <div class="contact__name">Tobias Lendhart</div>
      <div class="web">www.tobiaslendhart.de</div>
      <div class="contact__line">0162/3819204</div>
      <div class="contact__line">t.lendhart@mailpost.de</div>
      <div class="contact__line">Wiesengrundweg 14, 80417 München</div>
    </div>
    <div class="portrait" role="img" aria-label="Black and white portrait of the trainer with crossed arms"></div>
  </section>

</main>
</body>
</html>
```